One piece Trade show banner, 8' x 8' square

One piece banner for trade show
8' x 8' airborne geophysical company

Target Market(s)

Business

Industry/Entity Type

mineral exploration and science

Colors
0054AA
0677BA
7BADD7
CADEEF
E8F1F8
FFC000
F8CF3A
FAE287
FDF2CF
FEFAEE

Requirements
Must have
• Company logo (attached), slogan (Airborne Geophysics for Discovery). We are looking for a new banner, for a standard 8 x 8' square one-piece booth. I have attached some pictures, our logo, our old banner for reference, and two examples from unrelated companies from a tradeshow that we like. If its possible I'd like to change the color of the helicopter from green to dark grey. IE, keep the orange and white, just change green to dark grey. Looking for a simple, clean design with minimal text.
Nice to have
• I have attached examples of banners that we like (2xIMG), plus our old 3-piece banner r.
Should not have
• Green in the helicopter. Please change the color of the helicopter with green/orange/white to dark grey/orange/white. IE change the green to dark grey and leave the orange and white alone. I've attached lots of pictures but I don't expect them all to be used.

```html
<!DOCTYPE html>
<html lang="en">
<head>
<meta charset="utf-8">
<title>Northlight – Airborne Geophysics for Discovery</title>
<link rel="stylesheet" href="https://fonts.googleapis.com/css2?family=Nunito:ital,wght@0,800;0,900;1,900&family=Questrial&display=swap">
<style>
  :root {
    --blue-deep: #0054AA;
    --blue-mid: #0677BA;
    --blue-soft: #7BADD7;
    --gold: #FFC000;
    --gold-warm: #F8CF3A;
    --white: #FFFFFF;
    --photo-top: #3d4f96;
    --photo-mid: #5a5f98;
    --photo-low: #86718a;
  }
  * { margin: 0; padding: 0; box-sizing: border-box; }
  html, body { width: 1200px; height: 1200px; overflow: hidden; }
  body {
    position: relative;
    background: var(--blue-deep);
    font-family: "Questrial", "Century Gothic", sans-serif;
    color: var(--white);
  }
  .banner-art { position: absolute; inset: 0; width: 1200px; height: 1200px; }

  .slogan {
    position: absolute;
    left: 70px;
    top: 118px;
    width: 560px;
    transform: rotate(-7.5deg);
    transform-origin: left top;
  }
  .slogan__rule-top {
    position: absolute; left: 26px; top: -4px;
    width: 500px; height: 5px;
    background: linear-gradient(90deg, rgba(255,192,0,0) 0%, var(--gold) 30%, var(--gold) 100%);
  }
  .slogan__line-one {
    position: absolute; left: 0; top: 4px;
    font-family: "Nunito", sans-serif;
    font-style: italic; font-weight: 900;
    font-size: 51px; letter-spacing: 1px;
    white-space: nowrap;
    text-shadow: 0 2px 6px rgba(0,0,0,0.35);
  }
  .slogan__for {
    position: absolute; left: 108px; top: 104px;
    font-family: "Questrial", sans-serif;
    font-size: 30px; color: var(--gold);
  }
  .slogan__line-two {
    position: absolute; left: 162px; top: 58px;
    font-family: "Nunito", sans-serif;
    font-style: italic; font-weight: 900;
    font-size: 86px; letter-spacing: 1px;
    white-space: nowrap;
    text-shadow: 0 3px 8px rgba(0,0,0,0.35);
  }
  .slogan__rule-bottom {
    position: absolute; left: 168px; top: 170px;
    width: 370px; height: 12px;
    background: linear-gradient(90deg, var(--gold) 0%, var(--gold) 55%, rgba(255,192,0,0) 100%);
    clip-path: polygon(0 0, 100% 40%, 100% 60%, 0 100%);
  }

  .brand {
    position: absolute; right: 102px; top: 86px;
    font-family: "Questrial", sans-serif;
    font-size: 60px; line-height: 1; letter-spacing: 1px;
    color: var(--white);
  }

  .services { position: absolute; width: 520px; }
  .services--left { left: 115px; top: 719px; }
  .services--right { left: 565px; top: 713px; }
  .service + .service { margin-top: 42px; }
  .service__title {
    font-family: "Nunito", sans-serif; font-weight: 800;
    font-size: 37px; line-height: 42px;
    color: var(--gold);
  }
  .service__list { list-style: none; }
  .service__item {
    position: relative;
    padding-left: 31px;
    font-size: 34px; line-height: 42px;
    white-space: nowrap;
  }
  .service__item::before {
    content: ""; position: absolute;
    left: 4px; top: 19px;
    width: 8px; height: 8px; border-radius: 50%;
    background: var(--white);
  }

  .web-address {
    position: absolute; right: 104px; top: 1136px;
    padding: 0 16px;
    background: var(--blue-deep);
    font-size: 28px; line-height: 38px; letter-spacing: 0.5px;
  }
</style>
</head>
<body>
  <svg class="banner-art" viewBox="0 0 1200 1200" xmlns="http://www.w3.org/2000/svg">
    <defs>
      <linearGradient id="mountainTone" x1="0" y1="0" x2="0.3" y2="1">
        <stop offset="0" stop-color="#3d4f96"/>
        <stop offset="0.5" stop-color="#5a5f98"/>
        <stop offset="1" stop-color="#86718a"/>
      </linearGradient>
    </defs>
    <path class="swoosh" fill="#FFFFFF"
      d="M0,62 H1200 V292 C1060,522 860,665 620,665 C350,665 120,520 0,332 Z"/>
    <path class="hero-photo" role="img"
      aria-label="Photo: survey helicopter with sensor booms flying over snowy rocky mountains at sunset"
      fill="url(#mountainTone)"
      d="M0,62 H1200 V238 C1060,470 860,622 620,622 C360,624 130,480 0,298 Z"/>
    <rect class="frame" x="45" y="45" width="1110" height="1110" rx="38"
      fill="none" stroke="#FFFFFF" stroke-width="2.5"/>
  </svg>

  <div class="brand">Northlight</div>

  <div class="slogan">
    <div class="slogan__rule-top"></div>
    <div class="slogan__line-one">Airborne Geophysics</div>
    <div class="slogan__for">for</div>
    <div class="slogan__line-two">Discovery</div>
    <div class="slogan__rule-bottom"></div>
  </div>

  <div class="services services--left">
    <section class="service">
      <h2 class="service__title">Electromagnetics</h2>
      <ul class="service__list">
        <li class="service__item">Frequency domain</li>
        <li class="service__item">Time domain</li>
        <li class="service__item">Passive</li>
      </ul>
    </section>
    <section class="service">
      <h2 class="service__title">Radiometrics</h2>
      <ul class="service__list">
        <li class="service__item">256/512 channels</li>
        <li class="service__item">Up to 33 litres</li>
      </ul>
    </section>
  </div>

  <div class="services services--right">
    <section class="service">
      <h2 class="service__title">Magnetics</h2>
      <ul class="service__list">
        <li class="service__item">Helicopter, fixed wing, and drone</li>
        <li class="service__item">Total field and gradient</li>
      </ul>
    </section>
    <section class="service">
      <h2 class="service__title">Consulting</h2>
      <ul class="service__list">
        <li class="service__item">Survey design</li>
        <li class="service__item">Interpretations</li>
        <li class="service__item">Inversions</li>
      </ul>
    </section>
  </div>

  <div class="web-address">www.northlightsurveys.com</div>
</body>
</html>
```